Dunmore Roofing

Want a professional looking business card

Industry/Entity Type

Business

Contact Information for Business Card

Paul Dunmore ( Owner) paul@dunmoreroofing-example.com, www.dunmoreroofing-example.com, Adress: 4172 Township road 43 Ashbury,ON K9X4T2

```html
<!DOCTYPE html>
<html lang="en">
<head>
<meta charset="utf-8">
<title>Dunmore Roofing – Business Cards</title>
<link rel="stylesheet" href="https://fonts.googleapis.com/css2?family=Source+Sans+3:wght@400;600;700&display=swap">
<style>
  :root {
    --backdrop: #808285;
    --brand-blue: #1b4586;
    --brand-blue-light: #21509a;
    --band-grey: #7b7c7f;
    --icon-grey: #8a8b8e;
    --white: #ffffff;
    --mist: #c9ced8;
  }
  * { box-sizing: border-box; margin: 0; padding: 0; }
  html, body { width: 1200px; height: 828px; overflow: hidden; }
  body {
    background: var(--backdrop);
    font-family: "Source Sans 3", Arial, sans-serif;
    position: relative;
  }
  .card {
    position: absolute;
    width: 547px;
    height: 312px;
    overflow: hidden;
  }
  .card--front-a { left: 315px; top: 65px; }
  .card--front-b { left: 40px; top: 428px; }
  .card--back { left: 615px; top: 426px; background: var(--brand-blue); }
  .card__art { position: absolute; inset: 0; }

  .card__illustration {
    position: absolute;
    left: 300px; top: 0;
    width: 247px; height: 170px;
    background: linear-gradient(225deg, var(--brand-blue) 0%, var(--mist) 45%, var(--white) 100%);
  }

  .brand {
    position: absolute;
    left: 24px;
    top: 68px;
    display: flex;
    align-items: center;
    gap: 10px;
    color: var(--brand-blue);
    font-weight: 700;
    font-size: 30px;
    letter-spacing: 0.5px;
    text-transform: uppercase;
    white-space: nowrap;
  }
  .brand__mark {
    width: 16px; height: 16px;
    background: var(--brand-blue);
    flex: none;
  }

  .person {
    position: absolute;
    left: 28px;
    top: 216px;
    color: var(--white);
  }
  .person__name { font-size: 19px; font-weight: 700; line-height: 1.2; }
  .person__role { font-size: 15px; font-weight: 400; margin-top: 6px; }

  .contact {
    position: absolute;
    left: 285px;
    top: 206px;
    list-style: none;
    color: var(--white);
    font-size: 14px;
    line-height: 19.5px;
    white-space: nowrap;
  }
  .contact__item { display: flex; align-items: flex-start; gap: 6px; }
  .contact__icon { width: 15px; height: 15px; margin-top: 2px; flex: none; }

  .back__map {
    position: absolute;
    left: 95px; top: 20px;
    width: 360px; height: 230px;
    background: radial-gradient(ellipse at center, rgba(255,255,255,0.08), rgba(255,255,255,0) 70%);
  }
  .back__brand {
    position: absolute;
    left: 0; right: 0; top: 128px;
    display: flex;
    justify-content: center;
    align-items: center;
    gap: 12px;
    color: var(--white);
    font-weight: 700;
    font-size: 34px;
    letter-spacing: 1px;
    text-transform: uppercase;
    white-space: nowrap;
  }
  .back__brand .brand__mark { background: var(--white); width: 18px; height: 18px; }
  .back__web {
    position: absolute;
    left: 80px; right: 80px; top: 278px;
    display: flex; align-items: center; gap: 10px;
    color: var(--white);
    font-size: 14px;
    white-space: nowrap;
  }
  .back__rule { flex: 1; height: 1px; background: rgba(255,255,255,0.7); }
</style>
</head>
<body>

<section class="card card--front-a">
  <svg class="card__art" viewBox="0 0 547 312" aria-hidden="true">
    <rect width="547" height="312" fill="var(--white)"/>
    <rect y="170" width="547" height="17" fill="var(--band-grey)"/>
    <rect y="190" width="547" height="122" fill="var(--brand-blue)"/>
    <polygon points="190,312 300,190 547,190 547,312" fill="var(--brand-blue-light)" opacity="0.6"/>
    <polygon points="18,190 48,190 33,205" fill="var(--white)"/>
  </svg>
  <div class="card__illustration" role="img" aria-label="House roof illustration with window"></div>
  <div class="brand"><span class="brand__mark"></span>Dunmore Roofing</div>
  <div class="person">
    <p class="person__name">Paul Dunmore</p>
    <p class="person__role">Owner</p>
  </div>
  <ul class="contact">
    <li class="contact__item">
      <svg class="contact__icon" viewBox="0 0 16 16"><circle cx="8" cy="8" r="8" fill="var(--icon-grey)"/><path d="M5 4.5l1.5-.5 1 2-1 .8a5 5 0 0 0 2.7 2.7l.8-1 2 1-.5 1.5c-3.5.2-6.7-3-6.5-6.5z" fill="var(--white)"/></svg>
      (555) 014-2290</li>
    <li class="contact__item">
      <svg class="contact__icon" viewBox="0 0 16 16"><circle cx="8" cy="8" r="8" fill="var(--icon-grey)"/><rect x="4" y="5" width="8" height="6" fill="var(--white)"/><path d="M4 5l4 3.5L12 5" stroke="var(--icon-grey)" fill="none"/></svg>
      paul@dunmoreroofing-example.com</li>
    <li class="contact__item">
      <svg class="contact__icon" viewBox="0 0 16 16"><circle cx="8" cy="8" r="8" fill="var(--icon-grey)"/><circle cx="8" cy="8" r="4.2" fill="none" stroke="var(--white)"/><path d="M3.8 8h8.4M8 3.8v8.4" stroke="var(--white)"/></svg>
      www.dunmoreroofing-example.com</li>
    <li class="contact__item">
      <svg class="contact__icon" viewBox="0 0 16 16"><circle cx="8" cy="8" r="8" fill="var(--icon-grey)"/><path d="M8 13s-3.5-3.8-3.5-6a3.5 3.5 0 0 1 7 0c0 2.2-3.5 6-3.5 6z" fill="var(--white)"/><circle cx="8" cy="7" r="1.3" fill="var(--icon-grey)"/></svg>
      <span>4172 Township road 43, Ashbury,<br>ON K9X4T2</span></li>
  </ul>
</section>

<section class="card card--front-b">
  <svg class="card__art" viewBox="0 0 547 312" aria-hidden="true">
    <rect width="547" height="312" fill="var(--white)"/>
    <rect y="170" width="547" height="17" fill="var(--band-grey)"/>
    <rect y="190" width="547" height="122" fill="var(--band-grey)"/>
    <polygon points="292,190 547,190 547,312 195,312" fill="var(--brand-blue)"/>
    <polygon points="18,190 48,190 33,205" fill="var(--white)"/>
  </svg>
  <div class="card__illustration" role="img" aria-label="House roof illustration with window"></div>
  <div class="brand"><span class="brand__mark"></span>Dunmore Roofing</div>
  <div class="person">
    <p class="person__name">Paul Dunmore</p>
    <p class="person__role">Owner</p>
  </div>
  <ul class="contact">
    <li class="contact__item">
      <svg class="contact__icon" viewBox="0 0 16 16"><circle cx="8" cy="8" r="8" fill="var(--icon-grey)"/><path d="M5 4.5l1.5-.5 1 2-1 .8a5 5 0 0 0 2.7 2.7l.8-1 2 1-.5 1.5c-3.5.2-6.7-3-6.5-6.5z" fill="var(--white)"/></svg>
      (555) 014-2290</li>
    <li class="contact__item">
      <svg class="contact__icon" viewBox="0 0 16 16"><circle cx="8" cy="8" r="8" fill="var(--icon-grey)"/><rect x="4" y="5" width="8" height="6" fill="var(--white)"/><path d="M4 5l4 3.5L12 5" stroke="var(--icon-grey)" fill="none"/></svg>
      paul@dunmoreroofing-example.com</li>
    <li class="contact__item">
      <svg class="contact__icon" viewBox="0 0 16 16"><circle cx="8" cy="8" r="8" fill="var(--icon-grey)"/><circle cx="8" cy="8" r="4.2" fill="none" stroke="var(--white)"/><path d="M3.8 8h8.4M8 3.8v8.4" stroke="var(--white)"/></svg>
      www.dunmoreroofing-example.com</li>
    <li class="contact__item">
      <svg class="contact__icon" viewBox="0 0 16 16"><circle cx="8" cy="8" r="8" fill="var(--icon-grey)"/><path d="M8 13s-3.5-3.8-3.5-6a3.5 3.5 0 0 1 7 0c0 2.2-3.5 6-3.5 6z" fill="var(--white)"/><circle cx="8" cy="7" r="1.3" fill="var(--icon-grey)"/></svg>
      <span>4172 Township road 43, Ashbury,<br>ON K9X4T2</span></li>
  </ul>
</section>

<section class="card card--back">
  <div class="back__map" role="img" aria-label="Faint dotted world map in the background"></div>
  <div class="back__brand"><span class="brand__mark"></span>Dunmore Roofing</div>
  <div class="back__web"><span class="back__rule"></span>www.dunmoreroofing-example.com<span class="back__rule"></span></div>
</section>

</body>
</html>
```